Candy Bar Desgin

We need a postcard desgin for my new company. I just started a Candy bar/buffet called Sweet table By Mimi. My motto is Sweet Table by Mimi for the tiny tab. I will be attending a bridal show where I can display my work so there will be brides there. So I want something to pop. Maybe can add vases filled with candy. Add 20% off an event you book for attending the bridal show. I want colors. Candy colors. My company also do chocolate fountain bars as well. My website to add is www.sweettablebymimi.com
Email sweettablebymimi@fizzmail.com
Phone 323-555-0184

Target Market(s)

Brides

Industry/Entity Type

It Company

Requirements
Must have
• Must have my motto. And my contact information
Should not have
• No old style don't like times new roman. Use fun fonts

```html
<!DOCTYPE html>
<html lang="en">
<head>
<meta charset="utf-8">
<title>Sweet table By Mimi — Postcard</title>
<link href="https://fonts.googleapis.com/css2?family=Lobster+Two:ital,wght@1,700&family=Roboto:wght@700&family=Cherry+Swash:wght@400;700&display=swap" rel="stylesheet">
<style>
  :root{
    --candy-red:#e3141e;
    --deep-red:#c70d16;
    --white:#ffffff;
    --peach:#f6cdbd;
    --peach-light:#fbe2d6;
    --ink:#111111;
    --pink:#e8506f;
    --rose-frame:#f2a7b6;
    --page:#ececec;
  }
  *{margin:0;padding:0;box-sizing:border-box}
  html,body{width:1200px;height:722px;overflow:hidden;background:var(--page)}
  .canvas{position:relative;width:1200px;height:722px}
  .postcard{position:absolute;top:171px;width:560px;height:380px;overflow:hidden;
    background:radial-gradient(ellipse at 50% 45%,var(--peach-light),var(--peach));
    box-shadow:0 4px 14px rgba(0,0,0,.18)}
  .postcard--back{left:26px}
  .postcard--front{left:614px}
  .stripes{position:absolute;left:0;right:0;
    background:repeating-linear-gradient(90deg,var(--candy-red) 0 22px,var(--white) 22px 40px)}
  .stripes--top{top:0;height:34px}
  .stripes--bottom{bottom:0;height:62px}
  .rule{position:absolute;left:0;right:0;bottom:62px;height:10px;background:var(--ink)}
  .awning{position:absolute;left:0;right:0;top:34px;height:44px;background:var(--candy-red)}
  .awning::after{content:"";position:absolute;left:0;right:0;top:44px;height:10px;
    background:radial-gradient(circle at 10px 0,var(--candy-red) 10px,transparent 10.5px) 0 0/20px 10px repeat-x}
  .brand-title{position:absolute;top:42px;font-family:"Lobster Two",cursive;font-style:italic;font-weight:700;
    font-size:24px;color:var(--white);letter-spacing:.5px;white-space:nowrap}
  .postcard--back .brand-title{left:26px}
  .postcard--front .brand-title{left:0;right:0;text-align:center}
  .art{position:absolute;border-radius:6px}
  .art--couple{left:40px;top:96px;width:130px;height:130px;border-radius:50%;
    background:radial-gradient(circle,#f3e6de,#d8bda9);border:3px solid #c9a98a}
  .stamp-box{position:absolute;left:420px;top:40px;width:90px;height:74px;
    border:3px solid var(--white);background:rgba(255,255,255,.15)}
  .address-line{position:absolute;left:330px;width:190px;border-top:2px dashed #8a6a60}
  .label{position:absolute;background:var(--white);border-radius:40px;
    box-shadow:0 0 0 4px var(--white),0 0 0 6px var(--ink);display:flex;flex-direction:column;
    align-items:center;justify-content:center;text-align:center}
  .label::before{content:"";position:absolute;inset:5px;border:2px dashed var(--ink);border-radius:34px}
  .contact{left:28px;top:228px;width:236px;height:84px}
  .contact__phone{font-family:"Roboto",sans-serif;font-weight:700;font-size:24px;color:var(--candy-red)}
  .contact__line{font-family:"Roboto",sans-serif;font-weight:700;font-size:11px;color:var(--candy-red);line-height:1.3}
  .photo{position:absolute;border:5px solid var(--white);box-shadow:0 2px 6px rgba(0,0,0,.25)}
  .photo--dessert-table{left:34px;top:118px;width:130px;height:92px;transform:rotate(-3deg);
    background:linear-gradient(135deg,#e9b7c8,#b77e98)}
  .photo--cake{left:64px;top:222px;width:132px;height:90px;transform:rotate(-6deg);
    background:linear-gradient(135deg,#f5e3a8,#e98a8d)}
  .photo--candy-buffet{left:398px;top:90px;width:120px;height:78px;transform:rotate(3deg);
    background:linear-gradient(135deg,#f2c7a0,#c98a6c)}
  .photo--chocolate-fountain{left:404px;top:180px;width:110px;height:96px;transform:rotate(-3deg);
    background:linear-gradient(135deg,#d9b89a,#7a4a2c)}
  .offer{position:absolute;left:198px;top:100px;width:182px;height:122px;background:var(--white);
    border:6px solid var(--rose-frame);border-radius:10px;display:flex;flex-direction:column;
    align-items:center;justify-content:center;text-align:center;transform:rotate(-2deg)}
  .offer__headline{font-family:"Cherry Swash",cursive;font-size:34px;color:var(--candy-red);line-height:1}
  .offer__headline small{font-size:20px}
  .offer__terms{font-family:"Cherry Swash",cursive;font-size:12px;color:var(--candy-red);line-height:1.2;margin-top:4px}
  .motto{left:150px;top:262px;width:260px;height:80px}
  .motto__text{font-family:"Cherry Swash",cursive;font-size:20px;color:var(--ink);line-height:1.2}
  .motto__text .accent{color:var(--candy-red);font-family:"Lobster Two",cursive;font-style:italic;font-weight:700}
</style>
</head>
<body>
<main class="canvas">
  <section class="postcard postcard--back">
    <div class="stripes stripes--top"></div>
    <div class="awning"></div>
    <h1 class="brand-title">Sweet table By Mimi</h1>
    <div class="stamp-box"></div>
    <div class="art art--couple" role="img" aria-label="Illustration of a bride and groom"></div>
    <div class="address-line" style="top:150px"></div>
    <div class="address-line" style="top:182px"></div>
    <div class="address-line" style="top:214px"></div>
    <div class="address-line" style="top:246px"></div>
    <div class="rule"></div>
    <div class="stripes stripes--bottom"></div>
    <div class="label contact">
      <p class="contact__phone">323-555-0184</p>
      <p class="contact__line">www.sweettablebymimi.com</p>
      <p class="contact__line">sweettablebymimi@fizzmail.com</p>
    </div>
  </section>

  <section class="postcard postcard--front">
    <div class="stripes stripes--top"></div>
    <div class="awning"></div>
    <h2 class="brand-title">Sweet table By Mimi</h2>
    <div class="photo photo--dessert-table" role="img" aria-label="Photo of a pink dessert table"></div>
    <div class="photo photo--cake" role="img" aria-label="Photo of a layered cake"></div>
    <div class="photo photo--candy-buffet" role="img" aria-label="Photo of a candy buffet"></div>
    <div class="photo photo--chocolate-fountain" role="img" aria-label="Photo of a chocolate fountain with treats"></div>
    <div class="offer">
      <p class="offer__headline">20% <small>OFF</small></p>
      <p class="offer__terms">an event you book for<br>attending the bridal show</p>
    </div>
    <div class="rule"></div>
    <div class="stripes stripes--bottom"></div>
    <div class="label motto">
      <p class="motto__text"><span class="accent">Sweet Table</span> by Mimi<br>for the tiny tab</p>
    </div>
  </section>
</main>
</body>
</html>
```